Corporate Travel Technology Company needs new Business Card design

We need a new business card design to reflect our re-branded company. Our company is called tolvEn (pronounced tolvenn) and we provide Business Intelligence and Mobile Trip Coordination solutions for the corporate travel industry. Our multinational customers use our solutions to manage large travel budgets and frequent travellers, as well as to save money and reduce risk. We'd like to see designs that use the blue and green palette as well as our corporate logo (attached below). The design should communicate innovation, insight, forward thinking, contemporary, trusted.

Target Market(s)

Large multinational corporates and Travel Agencies.

Industry/Entity Type

Business

Contact Information for Business Card

Rosalind Mercer
Chief Executive
tolvEn
Phone number - +61 (0)2 8134 2907
Email address - rosalind.mercer@tolven-example.com
Mobile number - +61 (0)438 516 702
www.tolven-example.com

Font styles to use
Other font styles liked:
• Please use font as close to corporate logo as possible

Colors
0255a3
0393ce
00a990
33b8a4
33a6d7
3176b5

Requirements
Must have
• Please include the words;
• Mobile Trip Coordination
• Sharpening Corporate Journey Insight
• Use corporate logo - although icon can be stylised if needed

```html
<!DOCTYPE html>
<html lang="en">
<head>
<meta charset="utf-8">
<title>tolvEn – Business Card</title>
<link rel="stylesheet" href="https://fonts.googleapis.com/css2?family=Noto+Serif:wght@700&family=Open+Sans:wght@400;600&display=swap">
<style>
  :root {
    --page-bg: #ecebe8;
    --card-bg: #ffffff;
    --ink-dark: #3d4a52;
    --ink-grey: #5f6a70;
    --brand-blue: #0393ce;
    --card-edge: #dcdcdc;
    --card-shadow: rgba(40, 40, 40, 0.18);
  }
  * { margin: 0; padding: 0; box-sizing: border-box; }
  html, body { width: 1200px; height: 950px; overflow: hidden; }
  body {
    background: var(--page-bg);
    font-family: "Open Sans", Arial, sans-serif;
    position: relative;
  }
  .card {
    position: absolute;
    width: 640px;
    height: 380px;
    background: var(--card-bg);
    border-radius: 26px;
    box-shadow: 0 6px 0 var(--card-edge), 0 14px 30px var(--card-shadow);
  }
  .card--front { left: 280px; top: 60px; }
  .card--back  { left: 280px; top: 505px; }

  /* Front */
  .front-brand {
    position: absolute;
    top: 44px;
    right: 52px;
    display: flex;
    align-items: center;
    gap: 10px;
    color: var(--brand-blue);
    font-weight: 600;
    font-size: 26px;
  }
  .brand-dot {
    width: 22px; height: 22px;
    border-radius: 50%;
    background: var(--brand-blue);
  }
  .holder {
    position: absolute;
    left: 48px;
    bottom: 40px;
  }
  .holder__name {
    font-family: "Noto Serif", Georgia, serif;
    font-weight: 700;
    font-size: 27px;
    color: var(--ink-dark);
    line-height: 1.15;
  }
  .holder__title {
    font-family: "Noto Serif", Georgia, serif;
    font-weight: 700;
    font-size: 19px;
    color: var(--brand-blue);
    margin-bottom: 12px;
  }
  .contact {
    font-size: 13.5px;
    color: var(--ink-grey);
    line-height: 1.55;
  }
  .contact .sep { color: var(--brand-blue); padding: 0 5px; }
  .contact .bullet { color: var(--brand-blue); padding: 0 6px; }

  /* Back */
  .back-brand {
    position: absolute;
    inset: 0;
    display: flex;
    align-items: center;
    justify-content: center;
    gap: 16px;
  }
  .back-brand__name {
    font-weight: 400;
    font-size: 104px;
    letter-spacing: 2px;
    color: var(--ink-dark);
  }
  .back-brand .brand-dot {
    width: 40px; height: 40px;
    margin-top: -50px;
  }
</style>
</head>
<body>
  <section class="card card--front" aria-label="Business card front">
    <div class="front-brand"><span class="brand-dot"></span><span>tolvEn</span></div>
    <div class="holder">
      <h1 class="holder__name">Rosalind Mercer</h1>
      <p class="holder__title">Chief Executive</p>
      <div class="contact">
        <p>+61 (0)2 8134 2907<span class="sep">|</span>+61 (0)438 516 702</p>
        <p>rosalind.mercer@tolven-example.com<span class="sep">|</span>www.tolven-example.com</p>
        <p>Mobile Trip Coordination<span class="bullet">&bull;</span>Sharpening Corporate Journey Insight</p>
      </div>
    </div>
  </section>

  <section class="card card--back" aria-label="Business card back">
    <div class="back-brand">
      <span class="back-brand__name">tolvEn</span>
      <span class="brand-dot"></span>
    </div>
  </section>
</body>
</html>
```